New Business Card Design for Manufacturing

We are an engineering/manufacturing company that offers Advanced machining/assembly/engineering services, as well as innovative products for the heavy duty engine cooling markets.

We are looking to get a new business card designed that is clean and modern looking, but still fits the wide range of technical/skilled work we do.

- We hope to use this design as the base for other design work in new Presentations, web, and print work.

Industry/Entity Type

Engineering

Contact Information for Business Card

Our preferred color of blue is (RGB) 22/71/159 but can vary slightly from that color. Our content will be our Logo and full company name (Vantrell Forge Works, Inc.), company address, name, job title, phone number with extension, cell number, fax number, website, and email address on the cards.
We'd like the full company name next to the logo, but we are open to other interpretations of that layout.
Preferably, we would like the back side to be clean with just our logo, and the front to contain all of the contact information.

Colors
2f74b4
0355a3
85abd2

Requirements
Must have
• - Logo, company name, needed content - We are open to interpretation beyond that.
• - Standard size business card.
• - Horizontal orientation.
• - Enough space for lengthy names / job titles (for example, a job title could read "Directory of Human Resources" or "V.P. of Governmental Affairs"). We need this to look clean, whether the title be short (CEO) or long (as described above).

```html
<!DOCTYPE html>
<html lang="en">
<head>
<meta charset="utf-8">
<title>Vantrell Forge Works – Business Card</title>
<link href="https://fonts.googleapis.com/css2?family=Lato:ital,wght@0,400;0,700;0,900;1,400&display=swap" rel="stylesheet">
<style>
  :root {
    --brand-blue: #0355a3;
    --mid-blue: #2f74b4;
    --pale-blue: #85abd2;
    --paper: #ffffff;
    --ink: #111418;
    --backdrop: #e6e8eb;
  }
  * { box-sizing: border-box; margin: 0; padding: 0; }
  html, body { width: 1200px; height: 900px; overflow: hidden; }
  body {
    background: var(--backdrop);
    font-family: "Lato", Arial, sans-serif;
    position: relative;
  }
  .card {
    position: absolute;
    left: 280px;
    width: 640px;
    height: 366px;
    overflow: hidden;
    box-shadow: 0 6px 18px rgba(0,0,0,0.18);
  }

  /* Back side */
  .card-back {
    top: 48px;
    background: var(--brand-blue);
    color: var(--paper);
    display: flex;
    flex-direction: column;
    align-items: center;
    justify-content: center;
    text-align: center;
  }
  .back-wordmark {
    font-weight: 900;
    font-size: 78px;
    letter-spacing: 2px;
    line-height: 1;
    text-transform: uppercase;
  }
  .back-tagline {
    margin-top: 10px;
    font-weight: 900;
    font-size: 19px;
    letter-spacing: 3px;
    text-transform: uppercase;
  }
  .back-website {
    margin-top: 30px;
    font-size: 16px;
    letter-spacing: 1px;
  }

  /* Front side */
  .card-front {
    top: 474px;
    background: var(--paper);
  }
  .front-shape { position: absolute; inset: 0; }
  .brand-block {
    position: absolute;
    left: 34px;
    top: 34px;
    display: flex;
    align-items: flex-start;
    gap: 22px;
  }
  .brand-mark { color: var(--brand-blue); }
  .brand-wordmark {
    font-weight: 900;
    font-size: 46px;
    line-height: 1;
    letter-spacing: 1px;
    text-transform: uppercase;
  }
  .brand-tagline {
    margin-top: 6px;
    font-weight: 900;
    font-size: 11.5px;
    letter-spacing: 2px;
    text-transform: uppercase;
  }
  .company-name {
    margin-top: 30px;
    color: var(--ink);
    font-weight: 900;
    font-size: 16px;
    line-height: 1.05;
    text-transform: uppercase;
    letter-spacing: 0.5px;
  }
  .company-name .suffix { font-size: 9px; }
  .address {
    position: absolute;
    left: 30px;
    top: 220px;
    color: var(--paper);
    font-size: 15px;
    line-height: 1.35;
  }
  .contact {
    position: absolute;
    right: 30px;
    top: 196px;
    color: var(--paper);
    text-align: right;
  }
  .person-name { font-weight: 700; font-size: 22px; line-height: 1.1; }
  .person-title { font-size: 15px; margin-bottom: 6px; }
  .contact-line {
    display: flex;
    justify-content: flex-end;
    align-items: center;
    gap: 10px;
    font-size: 14.5px;
    line-height: 1.45;
  }
  .contact-line svg { width: 14px; height: 14px; flex: none; }
</style>
</head>
<body>

  <section class="card card-back" aria-label="Card back">
    <div class="back-wordmark">Vantrell</div>
    <div class="back-tagline">Shaping What's Next</div>
    <div class="back-website">www.vantrellforge.com</div>
  </section>

  <section class="card card-front" aria-label="Card front">
    <svg class="front-shape" viewBox="0 0 640 366" preserveAspectRatio="none" aria-hidden="true">
      <path d="M0,150 Q330,270 640,135 L640,366 L0,366 Z" fill="var(--brand-blue)"/>
      <path d="M300,206 Q500,200 600,152 Q520,196 320,212 Z" fill="var(--pale-blue)"/>
    </svg>

    <div class="brand-block">
      <div class="brand-mark">
        <div class="brand-wordmark">Vantrell</div>
        <div class="brand-tagline">Shaping What's Next</div>
      </div>
      <div class="company-name">Vantrell<br>Forge<br>Works, <span class="suffix">Inc.</span></div>
    </div>

    <div class="address">418 Calder Row<br>Houston, TX 77041</div>

    <div class="contact">
      <div class="person-name">Dana Whitcombe</div>
      <div class="person-title">Directory of Human Resources</div>
      <div class="contact-line">512 555 0140
        <svg viewBox="0 0 16 16" aria-hidden="true"><path fill="#fff" d="M3.6 1.5l2.3 2.6-1.3 1.8c.9 2 2.5 3.6 4.5 4.5l1.8-1.3 2.6 2.3-1.2 2.1C7.8 13.3 2.7 8.2 1.5 2.7z"/></svg>
      </div>
      <div class="contact-line">512 555 0141
        <svg viewBox="0 0 16 16" aria-hidden="true"><rect x="4" y="1" width="8" height="14" rx="1.5" fill="none" stroke="#fff" stroke-width="1.5"/></svg>
      </div>
      <div class="contact-line">512 555 0143
        <svg viewBox="0 0 16 16" aria-hidden="true"><rect x="4" y="1" width="8" height="4" fill="#fff"/><rect x="1" y="6" width="14" height="6" rx="1" fill="#fff"/><rect x="4" y="10" width="8" height="5" fill="#fff" stroke="var(--brand-blue)"/></svg>
      </div>
      <div class="contact-line">info@vantrellforge.com
        <svg viewBox="0 0 16 16" aria-hidden="true"><rect x="1" y="3" width="14" height="10" fill="#fff"/><path d="M1 3l7 6 7-6" fill="none" stroke="var(--brand-blue)" stroke-width="1.2"/></svg>
      </div>
      <div class="contact-line">www.vantrellforge.com
        <svg viewBox="0 0 16 16" aria-hidden="true"><g fill="none" stroke="#fff" stroke-width="1.3"><circle cx="8" cy="8" r="6.5"/><ellipse cx="8" cy="8" rx="3" ry="6.5"/><path d="M1.5 8h13M2.5 4.8h11M2.5 11.2h11"/></g></svg>
      </div>
    </div>
  </section>

</body>
</html>
```